Northway Value Bureau (Account) WP Design

We need an Account (Profile) Wordpress design to add to nvb.co.uk.

The design should be based on https://nvb.co.uk/about/. The look and feel of the menu on the left.

The logic, after login the header menu will add another page:

Before Login:
Home / About / Trading / Support /

After Login
Home / About / Trading / Support / Account (Demo) - Logout

When you click on the / Account /

"Account Profile" page is loaded where you can change the settings etc.

"Account Profile" menu on the left should look the same as in / About / (https://nvb.co.uk/about/)

We need the following sub-pages under "Account Profile"

- Profile
- Transfers
- Reports
- Security
- API Key
- Affiliates

Now looking into each page:
-
- Profile (Should be split into individual or business) a user can choose whether how he want to run his account:

[Individual]

Personal Details
First Name:
Middle Name:
Family Name:
Citizenship:
Gender:
DOB:

[Attach File] (Government Issues ID, Passport, Driving License) - Verify

Contact Information
Phone: +44 207 555 0143 - Verify
E-Mail: sample@mailbox.example - Verify

Residential Address
Address line 1:
Address line 2:
Address line 3:
City:
Postcode:
Country:

[Attach File] (Utility Bill or Bank Statement) - Verify

[Business]

Company Name:
Registration Number:

Registered Address
Address line 1:
Address line 2:
Address line 3:
City:
Postcode:
Country:

[Attach File] (Certificate of Incorporation) - Verify
[Attach File] (Memorandum & Articles of Association)
[Attach File] (Shareholder Register)

Company Contact Information
Website:

-

- Transfers (Where a user can link a bank account to deposit or withdraw funds from the account)

Transfers

Add a bank account:

Please select the country where beneficiary’s bank is domicile: [Please select]
Please select the currency you wish to make transfers in: [Please select]

Full beneficiary name:
Full beneficiary address:
Beneficiary bank name:
Beneficiary bank address:
Beneficiary Bank Identification Code (BIC)/Routing Code:
Beneficiary IBAN number/account number:

[SAVE]

Deposti funds to NVB Bank Account
Amount of currency to be received e.g. 2345.67 [Please select: USD, EUR, GBP] :
Full beneficiary name: Northway Value Bureau Limited
Full beneficiary address: Kestrel Court
7-9 Fenwick Row
London, United Kingdom
Beneficiary bank name:
Beneficiary bank address:
Beneficiary Bank Identification Code (BIC)/Routing Code: XXXXXXXXXX
Beneficiary IBAN number/account number: XXXXXXXXXXXXXXXXXXXXXXXXXX

Deposit coins to NVB Coin Account
Amount of coins to be received e.g. 2345.67 [Please select: BTC, LTC]:
NVB Coin Account: XXXXXXXXXXXXXXXXXXXXXXXXXXXXX

Applicable charges (?):
[Clear] [Continue]

Withdraw funds from NVB Bank Account
Amount of currency to be sent e.g. 2345.67 [Please select: USD, EUR, GBP] :

Withdraw coins from NVB Coin Account:
Amount of coins to be sent e.g. 2345.67 [Please select: BTC, LTC]:
Please specify you coin account: XXXXXXXXXXXXXXXXXXXXXXXXXXXXX

Applicable charges (?):
[Clear] [Continue]

-

- Reports

TBC
-

- Security

Change Password
Current Password:
New Password:
Confirm New Password:

Enable / Disable : Two-factor Authentication (SMS)

-

- API Key
TBC

-
- Affiliates

Unlimited earning potential!
You'll receive up to 10% commission on all trades made through your affiliate link.

Referral Circle Scheme
Simply apply to our program from your publisher account or click the "Join Now" button below.

Corvalent.com - Join Now

```html
<!DOCTYPE html>
<html lang="en">
<head>
<meta charset="utf-8">
<title>Northway Value Bureau – Account Profile</title>
<link href="https://fonts.googleapis.com/css2?family=Roboto:wght@400;500;700&display=swap" rel="stylesheet">
<style>
:root{
  --frame:#333333;
  --page:#ffffff;
  --brand:#0099d4;
  --brand-dark:#1a8ac0;
  --ink:#222222;
  --muted:#666666;
  --soft:#8a8a8a;
  --line:#cccccc;
  --dark-btn:#444444;
}
*{box-sizing:border-box;margin:0;padding:0}
html,body{width:1043px;height:1200px;overflow:hidden;background:var(--frame);font-family:"Roboto",Arial,sans-serif;color:var(--ink)}
.page{position:absolute;left:57px;top:0;width:930px;height:1172px;background:var(--page)}
.abs{position:absolute}
.brand{position:absolute;display:flex;align-items:center;gap:8px}
.brand-name{font-size:9px;letter-spacing:4px;line-height:15px;width:120px;text-transform:uppercase;color:#333}
.brand-dot{width:12px;height:12px;border-radius:50%;background:var(--brand)}
.brand-rule{width:1px;background:#333;height:52px}
.nav{left:221px;top:50px;font-size:10px;color:#555}
.login-field{height:19px;border:1px solid var(--line);font-size:9.5px;color:#999;padding:3px 4px;display:flex;justify-content:space-between;align-items:center}
.login-field i{width:12px;height:12px;border:1px solid #bbb;border-radius:50%;font-style:normal;font-size:8px;text-align:center;line-height:10px;color:#aaa}
.btn{position:absolute;height:19px;border-radius:2px;font-size:8.5px;color:#fff;display:flex;align-items:center;justify-content:center;font-weight:500}
.btn-dark{background:var(--dark-btn)}
.btn-brand{background:var(--brand)}
.ticker{position:absolute;left:0;top:79px;width:930px;height:38px;background:var(--brand);color:#fff}
.ticker .coin{position:absolute;left:184px;top:6px;width:26px;height:26px;border-radius:50%;border:2px solid #fff}
.tick{position:absolute;top:6px}
.tick small{display:block;font-size:8px}
.tick b{font-weight:400;font-size:11px}
.tick em{font-style:normal;font-size:8px}
.tick-rule{position:absolute;top:0;width:1px;height:38px;background:rgba(255,255,255,.6)}
.title{left:167px;top:162px;font-size:16px;font-weight:500}
.side{position:absolute;right:638px;text-align:right;font-size:12.5px;font-weight:500;color:var(--soft)}
.side.active{color:var(--ink)}
.side-bar{left:256px;top:198px;width:2px;height:21px;background:#333}
.radio{position:absolute;top:204px;display:flex;align-items:center;gap:7px;font-size:11.5px;color:#333}
.radio span{width:10px;height:10px;border:1px solid #999;border-radius:50%;display:inline-block;position:relative}
.radio.on span::after{content:"";position:absolute;left:2px;top:2px;width:4px;height:4px;border-radius:50%;background:var(--brand)}
.label{position:absolute;right:513px;font-size:11.5px;color:#333;text-align:right;transform:translateY(-50%)}
.field{position:absolute;left:433px;width:165px;height:22px;border:1px solid var(--line);transform:translateY(-50%);font-size:10px;color:#777;padding:0 10px;display:flex;align-items:center;justify-content:space-between}
.field.wide{width:211px}
.field.select{color:#333}
.section{position:absolute;left:339px;font-size:11.5px;font-weight:700;transform:translateY(-50%)}
.verify{position:absolute;left:602px;width:59px;height:20px;transform:translateY(-50%);background:var(--brand);color:#fff;font-size:9.5px;font-weight:700;display:flex;align-items:center}
.verify span{width:20px;height:20px;background:var(--brand-dark);display:flex;align-items:center;justify-content:center;margin-right:6px}
.dial{display:flex;align-items:center;gap:3px;background:#eee;height:20px;margin-left:-10px;padding:0 5px;border-right:1px solid var(--line);color:#333}
.flag{width:12px;height:8px;background:#9aa6c4}
.footer{position:absolute;left:0;top:916px;width:930px;height:256px;background:var(--brand);color:#fff}
.footer .brand-name{color:#fff}
.footer .brand-rule{background:#fff}
.footer .brand-dot{background:#fff}
.foot-head{position:absolute;top:32px;font-size:17px;font-weight:700}
.foot-links{position:absolute;top:65px;font-size:9.5px;line-height:11.7px;list-style:none}
.copy{left:86px;top:95px;font-size:8px;line-height:11px}
.social{position:absolute;top:61px;width:22px;height:22px;border-radius:50%;background:#fff}
.motto{position:absolute;left:391px;top:163px;width:444px;height:56px;background:linear-gradient(90deg,rgba(255,255,255,.15),rgba(255,255,255,.3));border-radius:4px}
</style>
</head>
<body>
<div class="page">
  <header>
    <div class="brand" style="left:86px;top:14px">
      <div class="brand-name">Northway Value Bureau</div>
      <div class="brand-rule"></div>
      <div class="brand-dot"></div>
    </div>
    <div class="abs nav">Home · About · Trading · Support · Account (Demo) - Logout</div>
    <div class="abs login-field" style="left:538px;top:31px;width:101px">Email<i>?</i></div>
    <div class="abs login-field" style="left:646px;top:31px;width:102px">Password<i>?</i></div>
    <div class="btn btn-dark" style="left:755px;top:31px;width:42px">Log In</div>
    <div class="btn btn-brand" style="left:801px;top:31px;width:42px">Sign Up</div>
  </header>

  <div class="ticker">
    <div class="coin"></div>
    <div class="tick" style="left:219px"><small>Current Price</small><b>$444.13</b></div>
    <div class="tick-rule" style="left:287px"></div>
    <div class="tick" style="left:307px"><small>Daily Change</small><b>-9.54</b> <em>2.10%</em></div>
    <div class="tick-rule" style="left:385px"></div>
    <div class="tick" style="left:404px"><small>Day's Range</small><b>$440.00 - $457.30</b></div>
    <div class="tick-rule" style="left:515px"></div>
    <div class="tick" style="left:534px"><small>Today's Open</small><b>$453.57</b></div>
    <div class="tick-rule" style="left:606px"></div>
    <div class="tick" style="left:625px"><small>24h Volume</small><b>7194 BTC</b></div>
  </div>

  <main>
    <h1 class="abs title">Account Profile</h1>
    <nav>
      <div class="side active" style="top:201px">Profile</div>
      <div class="side" style="top:226px">Transfers</div>
      <div class="side" style="top:250px">Reports</div>
      <div class="side" style="top:276px">Security</div>
      <div class="side" style="top:300px">API Key</div>
      <div class="side" style="top:325px">Affiliates</div>
      <div class="abs side-bar"></div>
    </nav>

    <div class="radio" style="left:327px"><span></span>Individual</div>
    <div class="radio on" style="left:403px"><span></span>Business</div>

    <div class="label" style="top:279px">Company Name:</div><div class="field" style="top:279px"></div>
    <div class="label" style="top:310px">Registration Number:</div><div class="field" style="top:310px"></div>

    <div class="section" style="top:345px">Registered Address</div>
    <div class="label" style="top:379px">Address line 1:</div><div class="field" style="top:379px"></div>
    <div class="label" style="top:411px">Address line 2:</div><div class="field" style="top:411px"></div>
    <div class="label" style="top:441px">Address line 3:</div><div class="field" style="top:441px"></div>
    <div class="label" style="top:472px">City:</div><div class="field" style="top:472px"></div>
    <div class="label" style="top:503px">Postcode:</div><div class="field" style="top:503px"></div>
    <div class="label" style="top:534px">Country:</div>
    <div class="field select" style="top:534px">United Kingdom
      <svg width="10" height="6" viewBox="0 0 10 6"><path d="M1 1l4 4 4-4" fill="none" stroke="#555" stroke-width="1.2"/></svg></div>

    <div class="label" style="top:566px">Attach File:</div>
    <div class="field" style="top:566px">Certificate of Incorporation
      <svg width="14" height="12" viewBox="0 0 14 12"><path d="M3 9l5-6a2 2 0 013 3L6 11" fill="none" stroke="#888"/><path d="M11 8v4M9 10h4" stroke="#888"/></svg></div>
    <div class="verify" style="top:566px"><span><svg width="10" height="8" viewBox="0 0 10 8"><path d="M1 4l3 3 5-6" fill="none" stroke="#fff" stroke-width="1.3"/></svg></span>Verify</div>

    <div class="label" style="top:597px">Attach File:</div>
    <div class="field wide" style="top:597px">Memorandum &amp; Articles of Association
      <svg width="14" height="12" viewBox="0 0 14 12"><path d="M3 9l5-6a2 2 0 013 3L6 11" fill="none" stroke="#888"/><path d="M11 8v4M9 10h4" stroke="#888"/></svg></div>

    <div class="label" style="top:627px">Attach File:</div>
    <div class="field" style="top:627px">Shareholder Register
      <svg width="14" height="12" viewBox="0 0 14 12"><path d="M3 9l5-6a2 2 0 013 3L6 11" fill="none" stroke="#888"/><path d="M11 8v4M9 10h4" stroke="#888"/></svg></div>

    <div class="section" style="top:665px">Registered Address</div>
    <div class="label" style="top:705px">Phone:</div>
    <div class="field" style="top:705px;justify-content:flex-start;gap:7px;color:#333">
      <span class="dial"><span class="flag"></span>+44 ▾</span>207 555 0143</div>
    <div class="verify" style="top:705px"><span><svg width="10" height="8" viewBox="0 0 10 8"><path d="M1 4l3 3 5-6" fill="none" stroke="#fff" stroke-width="1.3"/></svg></span>Verify</div>

    <div class="label" style="top:736px">E-Mail:</div>
    <div class="field" style="top:736px">sample@mailbox.example</div>
    <div class="verify" style="top:736px"><span><svg width="10" height="8" viewBox="0 0 10 8"><path d="M1 4l3 3 5-6" fill="none" stroke="#fff" stroke-width="1.3"/></svg></span>Verify</div>

    <div class="label" style="top:766px">Website:</div><div class="field" style="top:766px"></div>
  </main>

  <footer class="footer">
    <div class="brand" style="left:86px;top:30px">
      <div class="brand-name">Northway Value Bureau</div>
      <div class="brand-rule" style="height:46px"></div>
      <div class="brand-dot"></div>
    </div>
    <p class="abs copy">© 2014 Northway Value Bureau.<br>All rights reserved</p>

    <h2 class="foot-head" style="left:349px">ABOUT US</h2>
    <ul class="foot-links" style="left:349px">
      <li>Rulebook</li><li>Trading Fees</li><li>Partners</li><li>Security</li><li>Terms of Service</li><li>Privacy Policy</li><li>Latest News</li>
    </ul>
    <h2 class="foot-head" style="left:547px">SUPPORT</h2>
    <ul class="foot-links" style="left:547px">
      <li>What is Bitcoin?</li><li>How to buy a bitcoin?</li><li>How to sell a bitcoin?</li>
    </ul>
    <h2 class="foot-head" style="left:725px">FOLLOW NVB</h2>
    <div class="social" style="left:725px"></div>
    <div class="social" style="left:756px"></div>
    <div class="social" style="left:787px"></div>
    <div class="social" style="left:818px"></div>

    <div class="motto" role="img" aria-label="Hand-lettered slogan: Change the world one bitcoin at a time"></div>
  </footer>
</div>
</body>
</html>
```